Dental clinic brochure design (Z fold)

We need a new brochure design made for our dental clinic - Corvellan Dental Surgery. One side is in English, the other is in Vietnamese - all text and translations provided in brochure sample with further instructions in word doc. We require a brochure design in a Z fold to convey a family friendly dental clinic, incorporating our logo colour into the theme and designers choice on complimentary colours. Additional high quality images are provided for use if required or free to use own images.

Colors
33b8a4
00a990
86cfc6

Requirements
Must have
• Easy to read font, flows from text to pictures and page to page
• At least 2 dental images

```html
<!DOCTYPE html>
<html lang="en">
<head>
<meta charset="utf-8">
<title>Corvellan Dental Surgery – Brochure Inside Spread</title>
<link href="https://fonts.googleapis.com/css2?family=Ubuntu:wght@400;500;700&display=swap" rel="stylesheet">
<style>
  :root {
    --teal: #00a990;
    --teal-bright: #33b8a4;
    --mint: #86cfc6;
    --mint-pale: #e4f2ef;
    --ink: #0e2f36;
    --grey: #555f63;
    --white: #ffffff;
    --page-bg: #e9eef8;
  }
  * { box-sizing: border-box; margin: 0; padding: 0; }
  html, body { width: 960px; height: 1200px; overflow: hidden; background: var(--page-bg); font-family: "Ubuntu", sans-serif; }
  .spread {
    position: absolute; left: 20px; top: 272px;
    width: 1497px; height: 1068px;
    transform: scale(0.6146); transform-origin: top left;
    background: var(--white);
    box-shadow: 0 4px 14px rgba(20, 40, 80, .12);
  }
  .abs { position: absolute; }
  .photo { position: absolute; }
  .photo--kids { left: 6px; top: 30px; width: 480px; height: 315px;
    background: linear-gradient(120deg, #e9b948 0%, #f2c9d3 40%, #d44a3c 60%, #c9d66a 100%); }
  .photo--braces { left: 65px; top: 695px; width: 878px; height: 373px; z-index: 2;
    background: linear-gradient(90deg, #ece6e2 0%, #c9bce8 30%, #e9c9b4 60%, #3a2a22 100%); }
  .strip-pale { left: 503px; top: 0; width: 26px; height: 695px; background: var(--mint-pale); }
  .panel-promos { left: 529px; top: 0; width: 438px; height: 1005px; background: var(--teal); }

  .scheme-title { left: 64px; top: 372px; color: var(--ink); font-weight: 700; line-height: 1.15; }
  .scheme-title .line1 { font-size: 36px; display: block; }
  .scheme-title .line2 { font-size: 47px; display: block; }
  .accent { color: var(--teal); }
  .scheme-body { left: 64px; top: 500px; width: 400px; font-size: 17px; line-height: 1.45; color: var(--grey); }
  .scheme-body strong { color: var(--ink); font-weight: 500; }
  .scheme-call { left: 64px; top: 596px; font-size: 17px; color: var(--grey); }
  .scheme-phone { left: 62px; top: 622px; font-size: 42px; font-weight: 700; color: var(--teal); }

  .promos-title { left: 553px; top: 186px; font-size: 44px; font-weight: 700; color: var(--white); line-height: 1.05; }
  .promo-list { left: 553px; top: 322px; width: 390px; list-style: none; color: var(--white); font-size: 17px; line-height: 1.45; }
  .promo-list li { position: relative; padding-left: 38px; margin-bottom: 33px; }
  .promo-list svg { position: absolute; left: 0; top: 3px; }
  .promo-list strong { font-weight: 700; }

  .providers-title { left: 1042px; top: 74px; font-size: 42px; font-weight: 700; color: var(--ink); }
  .provider { position: absolute; left: 1042px; display: flex; align-items: center; gap: 20px; }
  .provider .avatar { width: 52px; height: 52px; background: linear-gradient(180deg, var(--teal-bright), var(--mint)); }
  .provider .name { font-size: 25px; font-weight: 700; color: var(--ink); line-height: 1.1; }
  .provider .quals { font-size: 12px; color: var(--grey); margin-top: 3px; }

  .map { left: 1100px; top: 575px; width: 258px; height: 292px;
    background: linear-gradient(160deg, #f4f7f7, #dfe9e7); }
  .address-pale { left: 993px; top: 895px; width: 504px; height: 160px; background: var(--mint-pale); }
  .address-box { left: 1042px; top: 867px; width: 438px; height: 156px; background: var(--teal);
    color: var(--white); text-align: center; padding-top: 22px; font-size: 16.5px; line-height: 1.5; }
  .address-box h3 { font-size: 23px; font-weight: 700; margin-bottom: 8px; }
  .bottom-band { left: 993px; top: 1052px; width: 504px; height: 16px; background: var(--teal); }
</style>
</head>
<body>
  <main class="spread">
    <!-- Left panel: child scheme -->
    <div class="photo photo--kids" role="img" aria-label="Group of smiling children brushing their teeth"></div>
    <h2 class="abs scheme-title">
      <span class="line1"><span class="accent">Child</span> Dental Scheme</span>
      <span class="line2"><span class="accent">Benefits</span> Schedule</span>
    </h2>
    <p class="abs scheme-body">A dental benefits program is available for eligible children aged 2 to 17 and will <strong>receive $1000</strong> for dental treatments.</p>
    <p class="abs scheme-call">To check if your children are eligible call us on</p>
    <p class="abs scheme-phone">(03) 9400 2618</p>

    <!-- Middle panel: promotions -->
    <div class="abs strip-pale"></div>
    <section class="abs panel-promos"></section>
    <h2 class="abs promos-title">Special<br>Promotions</h2>
    <ul class="abs promo-list">
      <li><svg width="20" height="20" viewBox="0 0 20 20"><circle cx="10" cy="10" r="8.5" fill="none" stroke="#fff" stroke-width="1.6"/><path d="M6 10.3l2.7 2.6L14 7.6" fill="none" stroke="#fff" stroke-width="1.8"/></svg>Gap free dental check-up, clean &amp; x-rays for all health insurances**</li>
      <li><svg width="20" height="20" viewBox="0 0 20 20"><circle cx="10" cy="10" r="8.5" fill="none" stroke="#fff" stroke-width="1.6"/><path d="M6 10.3l2.7 2.6L14 7.6" fill="none" stroke="#fff" stroke-width="1.8"/></svg>At home whitening kit <strong>now $199</strong> limited time only (normally $395)</li>
      <li><svg width="20" height="20" viewBox="0 0 20 20"><circle cx="10" cy="10" r="8.5" fill="none" stroke="#fff" stroke-width="1.6"/><path d="M6 10.3l2.7 2.6L14 7.6" fill="none" stroke="#fff" stroke-width="1.8"/></svg>*Conditions apply —<br>Ask staff for more information</li>
    </ul>
    <div class="photo photo--braces" role="img" aria-label="Smiling woman with braces at a dental check-up"></div>

    <!-- Right panel: providers -->
    <h2 class="abs providers-title">Dental Providers</h2>
    <div class="provider" style="top:175px"><div class="avatar" role="img" aria-label="Dentist avatar"></div><div><div class="name">Dr Linh Vo</div><div class="quals">BDSc (Melb), ICCDE</div></div></div>
    <div class="provider" style="top:250px"><div class="avatar" role="img" aria-label="Dentist avatar"></div><div><div class="name">Dr Bao Nguyen</div><div class="quals">BDSc (Melb), FICCDE FRACDS, PGradDipCD Implants (Melb)</div></div></div>
    <div class="provider" style="top:338px"><div class="avatar" role="img" aria-label="Dentist avatar"></div><div><div class="name">Dr Thu Ngo</div><div class="quals">BHsc Mdent (Latrobe)</div></div></div>
    <div class="provider" style="top:413px"><div class="avatar" role="img" aria-label="Dentist avatar"></div><div><div class="name">Dr Minh Ly</div><div class="quals">BHsc Mdent (Latrobe), FRACDS</div></div></div>
    <div class="provider" style="top:495px"><div class="avatar" role="img" aria-label="Dentist avatar"></div><div><div class="name">Dr Anh Doan</div><div class="quals">BDS (Adl)</div></div></div>

    <div class="abs map" role="img" aria-label="Street map showing the clinic location"></div>
    <div class="abs address-pale"></div>
    <div class="abs address-box">
      <h3>Address</h3>
      48 Larkfield Road Brenmore, VIC 3088<br>
      Phone: (03) 9400 2618<br>
      Email: admin@corvellandental.com.au
    </div>
    <div class="abs bottom-band"></div>
  </main>
</body>
</html>
```